Baby Boutique Needs a Business Card Design

We need a modern double sided business card design using the attached logo for Little Wren Nook.

Little Wren Nook is a baby boutique which sells only handmade clothing and accessories for both boys and girls. Our store will live exclusively online.

We would like to only use the colors that have been used in the logo.

Target Market(s)

Potential wholesale clients, Small business owners

Industry/Entity Type

Retail

Contact Information for Business Card

Name Gideon R. Falkner (Owner)
Email sales@littlewrennook.example
Main Phone 555-203-7719
Cell phone 555-203-7746
Website www.LittleWrenNook.example

Font styles to use
Sans Serif

Colors

Designer to choose colors to be used in the design.

Requirements
Must have
• -Would like to have icons that indentify the contact information.
• -Include our website
• -Include our tagline in a small area near the bottom. "Handmade Baby Creations"
• -Would like to include Facebook and Instagram Icons
• -
Nice to have
• Would like to have a simple back side with the logo.
• Something along the lines of the meadowfield lending card attached.

```html
<!DOCTYPE html>
<html lang="en">
<head>
<meta charset="utf-8">
<title>Little Wren Nook – Business Card</title>
<link rel="stylesheet" href="https://fonts.googleapis.com/css2?family=Arimo:wght@400;700&display=swap">
<style>
  :root {
    --bg: #e4e4e2;
    --card: #22272b;
    --teal: #78cbbd;
    --coral: #e35d5b;
    --white: #ffffff;
  }
  * { box-sizing: border-box; margin: 0; padding: 0; }
  html, body { width: 1200px; height: 1189px; overflow: hidden; }
  body {
    background: var(--bg);
    font-family: "Arimo", Arial, sans-serif;
    position: relative;
  }
  .card {
    position: absolute;
    left: 170px;
    width: 860px;
    height: 491px;
    background: var(--card);
    border-radius: 26px;
    overflow: hidden;
    box-shadow: 0 10px 30px rgba(0,0,0,0.25);
  }
  .card--back { top: 80px; }
  .card--front { top: 618px; }

  .brand-name {
    position: absolute;
    color: var(--teal);
    font-weight: 700;
    line-height: 1.02;
  }
  .card--back .brand-name {
    left: 0; right: 0; top: 120px;
    text-align: center;
    font-size: 58px;
  }
  .brand-mark {
    display: inline-block;
    width: 18px; height: 18px;
    border-radius: 50%;
    background: var(--coral);
    margin-left: 10px;
    vertical-align: middle;
  }

  .back-rule {
    position: absolute;
    top: 316px; height: 2px;
    background: var(--coral);
  }
  .back-rule--left { left: 0; width: 444px; }
  .back-rule--right { left: 548px; right: 0; }
  .social {
    position: absolute;
    top: 296px; left: 456px;
    display: flex; gap: 12px;
  }
  .social span {
    width: 40px; height: 40px;
    background: var(--teal);
    border-radius: 3px;
  }

  .card--front .brand-name {
    left: 48px; top: 150px; width: 320px;
    font-size: 54px;
  }
  .divider {
    position: absolute;
    left: 404px; top: 88px;
    width: 2px; height: 222px;
    background: var(--teal);
  }
  .contact {
    position: absolute;
    left: 452px; top: 96px;
  }
  .contact__name {
    color: var(--teal);
    font-weight: 700;
    font-size: 27px;
  }
  .contact__role {
    color: var(--coral);
    font-size: 20px;
    margin: 2px 0 16px;
  }
  .contact__list { list-style: none; }
  .contact__list li {
    display: flex; align-items: center; gap: 12px;
    color: var(--teal);
    font-size: 21px;
    line-height: 31px;
  }
  .contact__list svg { width: 20px; height: 20px; flex: none; }

  .front-rule {
    position: absolute;
    left: 0; right: 0; top: 370px;
    height: 4px;
    background: var(--coral);
  }
  .tagline-band {
    position: absolute;
    left: 0; right: 0; top: 380px; bottom: 0;
    background: var(--teal);
    display: flex; align-items: center; justify-content: center;
  }
  .tagline {
    color: var(--white);
    font-size: 25px;
    letter-spacing: 8px;
  }
</style>
</head>
<body>

<section class="card card--back" aria-label="Card back">
  <div class="brand-name">Little Wren Nook<span class="brand-mark"></span></div>
  <div class="back-rule back-rule--left"></div>
  <div class="social" aria-label="Social profiles"><span></span><span></span></div>
  <div class="back-rule back-rule--right"></div>
</section>

<section class="card card--front" aria-label="Card front">
  <div class="brand-name">Little<br>Wren Nook<span class="brand-mark"></span></div>
  <div class="divider"></div>
  <div class="contact">
    <div class="contact__name">Gideon R. Falkner</div>
    <div class="contact__role">Owner</div>
    <ul class="contact__list">
      <li>
        <svg viewBox="0 0 20 20" aria-hidden="true"><path fill="#e35d5b" d="M2 7c0-3 4-4 8-4s8 1 8 4v2h-4V7H6v2H2zM5 10h10l2 7H3z"/></svg>
        555-203-7719
      </li>
      <li>
        <svg viewBox="0 0 20 20" aria-hidden="true"><rect x="5" y="1.5" width="10" height="17" rx="1.5" fill="none" stroke="#e35d5b" stroke-width="2"/><circle cx="10" cy="15" r="1" fill="#e35d5b"/></svg>
        555-203-7746
      </li>
      <li>
        <svg viewBox="0 0 20 20" aria-hidden="true"><rect x="1" y="4" width="18" height="12" fill="#e35d5b"/><path d="M1 4l9 7 9-7" fill="none" stroke="#22272b" stroke-width="1.5"/></svg>
        sales@littlewrennook.example
      </li>
      <li>
        <svg viewBox="0 0 20 20" aria-hidden="true"><g fill="none" stroke="#e35d5b" stroke-width="1.6"><circle cx="10" cy="10" r="8"/><ellipse cx="10" cy="10" rx="3.5" ry="8"/><path d="M2 10h16M3.5 6h13M3.5 14h13"/></g></svg>
        www.LittleWrenNook.example
      </li>
    </ul>
  </div>
  <div class="front-rule"></div>
  <div class="tagline-band"><span class="tagline">Handmade Baby Creations</span></div>
</section>

</body>
</html>
```